Business card design for new eCommerce site focusing on integrity and strong businsess tactics

We need a business card that will stand out and be memorable. Something with color that matches our company logo colors. Think high end version of Pactivo. There are 2 logos provided. The parent company is called Amber Ledge Partners and we are presenting a new and very exciting eCommerce site called BrightHarborTrade.example.

Target Market(s)

Our target markets are in the Activities, Food and Beverage, Health and Beauty

Industry/Entity Type

Marketing

Contact Information for Business Card

We have 4 members that need cards...I will provide all info to the winner of the design contest
Business Address is
4870 West 63rd Avenue, Suite C207
Phoenix AZ 85731

Font styles to use
Serif
Sans Serif

Colors

Designer to choose colors to be used in the design.

Requirements
Must have
• The card must be memorable...should be unique in design but must exude integrity and be playful .
• I have provided several colors or our parent company...please feel free to use which ever
Nice to have
• I will leave this up to you. Feel free to use other images of your choosing that wraps around our client.....Activities, Dining, Health, Beauty
Should not have
• just dont be boring

```html
<!DOCTYPE html>
<html lang="en">
<head>
<meta charset="utf-8">
<title>Amber Ledge Partners – Business Card</title>
<link href="https://fonts.googleapis.com/css2?family=Montserrat:wght@400;500;600;700&display=swap" rel="stylesheet">
<style>
  :root {
    --backdrop: #161616;
    --card: #232323;
    --card-edge: #2b2b2b;
    --teal: #3aa6a0;
    --ink: #f1f1f1;
    --emboss: #7d7d7d;
    --emboss-soft: #5f5f5f;
  }
  * { margin: 0; padding: 0; box-sizing: border-box; }
  html, body {
    width: 1200px; height: 900px; overflow: hidden;
    background: var(--backdrop);
    font-family: "Montserrat", sans-serif;
  }
  .canvas {
    width: 1200px; height: 900px;
    display: flex; flex-direction: column; align-items: center; justify-content: center;
    gap: 40px;
  }
  .card {
    width: 700px; height: 400px;
    background: linear-gradient(135deg, var(--card) 0%, var(--card-edge) 100%);
    position: relative;
    box-shadow: 0 10px 30px rgba(0,0,0,.5);
  }
  /* Front card */
  .front-brand {
    position: absolute; left: 0; right: 0; top: 130px;
    display: flex; align-items: center; justify-content: center; gap: 14px;
  }
  .front-brand .mark {
    width: 22px; height: 22px; border-radius: 50%; background: var(--emboss-soft);
  }
  .front-brand .name {
    font-size: 34px; font-weight: 500; color: var(--emboss); letter-spacing: .5px;
  }
  .front-tagline {
    position: absolute; left: 0; right: 0; top: 182px; text-align: center;
    font-size: 15px; letter-spacing: 2px; color: var(--emboss-soft);
  }
  .front-url {
    position: absolute; left: 0; right: 0; bottom: 48px; text-align: center;
    font-size: 14px; letter-spacing: 2px; color: var(--ink);
  }
  /* Back card */
  .back-brand {
    position: absolute; left: 60px; top: 120px; width: 260px;
    display: flex; flex-direction: column; align-items: center; gap: 16px;
  }
  .back-brand .mark {
    width: 56px; height: 56px; border-radius: 50%; border: 4px solid var(--teal);
  }
  .back-brand .name {
    font-size: 26px; font-weight: 700; color: var(--teal); text-align: center; line-height: 1.15;
  }
  .divider {
    position: absolute; left: 345px; top: 120px; width: 3px; height: 150px; background: var(--teal);
  }
  .contact {
    position: absolute; left: 375px; top: 122px;
  }
  .contact .person {
    font-size: 24px; font-weight: 700; color: var(--teal); letter-spacing: 1px;
  }
  .contact .role {
    font-size: 19px; color: var(--ink); margin-bottom: 18px;
  }
  .contact-list { list-style: none; }
  .contact-list li {
    display: flex; align-items: center; gap: 12px;
    font-size: 15px; color: var(--ink); letter-spacing: 1px; margin-bottom: 6px;
  }
  .contact-list svg { width: 16px; height: 16px; flex: none; }
  .address {
    position: absolute; left: 0; right: 0; bottom: 40px; text-align: center;
    font-size: 17px; color: var(--ink); letter-spacing: 1px;
  }
</style>
</head>
<body>
<main class="canvas">
  <section class="card card-front">
    <div class="front-brand">
      <span class="mark"></span>
      <span class="name">BrightHarborTrade.example</span>
    </div>
    <p class="front-tagline">Activities-Dining-Health-Beauty</p>
    <p class="front-url">www.amberledgepartners.example</p>
  </section>

  <section class="card card-back">
    <div class="back-brand">
      <span class="mark"></span>
      <span class="name">Amber Ledge Partners</span>
    </div>
    <div class="divider"></div>
    <div class="contact">
      <p class="person">Daniel Reyes</p>
      <p class="role">Founder</p>
      <ul class="contact-list">
        <li>
          <svg viewBox="0 0 16 16" aria-hidden="true"><rect x="4" y="1" width="8" height="14" rx="1.5" fill="none" stroke="#3aa6a0" stroke-width="1.5"/><line x1="7" y1="12.5" x2="9" y2="12.5" stroke="#3aa6a0" stroke-width="1.5"/></svg>
          0427 635 918
        </li>
        <li>
          <svg viewBox="0 0 16 16" aria-hidden="true"><rect x="1" y="3" width="14" height="10" rx="1" fill="#3aa6a0"/><path d="M1 4 L8 9 L15 4" fill="none" stroke="#232323" stroke-width="1.3"/></svg>
          info@brightharbortrade.example
        </li>
        <li>
          <svg viewBox="0 0 16 16" aria-hidden="true"><circle cx="6.5" cy="6.5" r="4.5" fill="none" stroke="#3aa6a0" stroke-width="2"/><line x1="10" y1="10" x2="14.5" y2="14.5" stroke="#3aa6a0" stroke-width="2.2"/></svg>
          www.brightharbortrade.example
        </li>
      </ul>
    </div>
    <p class="address">4870 West 63rd Avenue, Suite C207 Phoenix AZ 85731</p>
  </section>
</main>
</body>
</html>
```